website design + images

We need a very appealing website design, layout and images for a sales analytics and sales productivity services company based in San Ramon, California. We need a good design for the home page and a template for all other pages (total 2 designs), and images for all inner pages (center column/banner images, and right hand top corner small images). There are about 18 inner pages.
Updates

Our existing website is www.brightvale.com
Our corporate colours are the ones that are there on the website. The logo is also shown. We will be changing the tagline to "accelerating revenue" or equivalent of that.

Please use the document "website for brightvale - template v2.doc" that I just uploaded for any reference to the content, navigation and wireframes. A few more clarifications are provided mainly for the link "Solutions".

Rajesh Kothuri

Hi,
We just uploaded ver 4 of the website template. There is more elaboration provided around the sublinks / sections for Solutions. Pls review and do get back if you need any clarifications.

Rgds
Rajesh Kothuri

Hi all,
We have so far received a few good designs. The designs are more or less on the right track. I would like to urge all of you to use the content and navigation provided in the document attached to our brief "website for brightvale - template v4.doc".  Please DO NOT use the content in our existing website www.brightvale.com . That is very old. We mentioned it only for reference to colour theme and broad details.

We have totally 13 sections in Solutions pages. They may be designed as a tree of links - first level sublinks - second level sublinks or links - first level sublinks and the remaining as sections within the first level sublinks pages. The page design would remain the same for all inner pages except careers. But after finalizing the design for the inner page, we will need images for the different inner pages.

Rgds
Rajesh Kothuri

Hi,
Thank you all for participation and very good designs. We are quite happy with what we have seen. We have now shortlisted about 4 vendors and sending invididual feedback to them for further improvement. We will be finalizing by Monday or Tuesday.  To the vendors who do not get feedback from us, thank you very much for participation. We may still do business in future for some of our other needs. 
The following are the process steps / expectations going forward, 
1. Feedback to the shortlisted designers and inviting improvements.
2. Review of the improved designs and further shortlist & feedback or direct finalization.
3. The design should be in 1024*768
2. Number of page designs = 2 (home page, inner page).
4. Home page design: instead of delivery model and customers, show one link "Why Us".
4. Solutions page design:  We will be needing an image in center column of solutions page that in a nutshell gives all the different types of solutions we provide. The entire set of solutions is in our attached document website for brightvale - template v4 and I am just uploading v5 with more description on sublinks.
5. After selection, we will be needing images for all the solution pages (total 12 pages under solutions + one solutions page), 1 image for Why Us?, 1 for Careers, and 3 for company (about us/ team, core values, ...) = total 18

Rgds
Rajesh Kothuri

Target Market(s)

We are a sales analytics and sales productivity services company. We help B2B companies with: sales planning; sales operations and sales measurement. The characteristics of our customers are:
- B2B medium enterprises (USD 100M- USD 2B in revenue) in the US
- Primary target verticals are: high-tech, engineering and professional services firms
- Our primary target customers titles are VP of Sales or VP of marketing; we could be selling to the CEO at companies with revenues below $200M

Industry/Entity Type

Consulting

Requirements
Must have
• - Clean, uncluttered design
• - Easy navigation; minimum clicks
Nice to have
• We have already built a content management system and wireframes for this site. To the extent possible, it would be great to leverage the wireframe structure we built, provided you don’t have to compromise on the look and feel and navigation of the site. Below is what we currently have as banner sizes and resolutions are:
• Home page banner size: 950 * 250’
• All pages – center top - image size: 558 * 160
• All pages – right hand top image – 175*135’

```html
<!DOCTYPE html>
<html lang="en">
<head>
<meta charset="utf-8">
<title>BrightVale – Solutions</title>
<link rel="stylesheet" href="https://fonts.googleapis.com/css2?family=Arimo:wght@400;700&family=Roboto+Condensed:wght@700&family=Open+Sans:wght@600;700&display=swap">
<style>
:root{
  --blue:#0d6cb8;
  --blue-dark:#0a5a9c;
  --link:#0b66b5;
  --green:#4a9a3c;
  --green-band:rgba(74,154,60,.92);
  --text:#222;
  --line:#e3e3e3;
  --white:#fff;
}
*{box-sizing:border-box;margin:0;padding:0}
html,body{width:1200px;height:798px;overflow:hidden}
body{
  position:relative;
  font-family:"Arimo",Arial,sans-serif;
  color:var(--text);
  background:linear-gradient(#fff 0,#fff 120px,#e9e9e9 360px,#a9a9a9 640px,#8e8e8e 798px);
}
a{text-decoration:none;color:inherit}
.abs{position:absolute}

/* top utility bar */
.utility-bar{left:0;top:0;width:1200px;height:42px;background:linear-gradient(#1a7cc6,var(--blue-dark))}
.utility-nav{left:54px;top:0;display:flex;height:42px;align-items:center;font-size:13.5px;color:var(--white);letter-spacing:-.2px}
.utility-nav a{display:flex;align-items:center;gap:6px;padding:0 12px;height:42px}
.utility-nav a.signin{background:linear-gradient(#5fb34c,#3f8f35);height:50px;border-radius:0 0 4px 4px;margin-right:10px;box-shadow:0 1px 2px rgba(0,0,0,.3)}
.utility-nav svg{width:20px;height:20px}

/* page panel */
.page{left:48px;top:42px;width:1090px;height:708px;background:linear-gradient(#f6f6f6,#fff 90px);border-radius:0 0 12px 12px}

/* brand */
.brand-name{left:62px;top:108px;font-family:"Arimo",sans-serif;font-weight:700;font-size:28px;color:var(--blue)}

/* main nav */
.main-nav{left:746px;top:115px;display:flex;align-items:center;font-size:14px;font-weight:700;color:var(--blue)}
.main-nav a{padding:0 6px}
.main-nav .sep{font-weight:400;padding:0 2px}
.main-nav a.active{background:var(--green);color:var(--white);border-radius:13px;padding:4px 12px;margin:0 6px;box-shadow:inset 0 0 0 1px #2f7a28}

/* side navigation */
.side-nav{left:57px;top:185px;width:215px}
.side-head{height:38px;display:flex;align-items:center;gap:8px;padding-left:9px;font-family:"Roboto Condensed",sans-serif;font-size:14.5px;color:var(--green);background:linear-gradient(#fff,#dcdcdc);border:1px solid #d8d8d8;border-radius:4px 4px 0 0;margin-bottom:7px}
.side-head .toggle{width:16px;height:16px;background:var(--green);border-radius:2px;display:flex;align-items:center;justify-content:center}
.side-list{list-style:none;padding:8px 14px 6px;margin:-7px 0 8px;background:linear-gradient(#f3f3f3,#fff 30px)}
.side-list li{font-size:12px;height:25px;line-height:25px;border-bottom:1px dotted #aaa;padding-left:12px;position:relative}
.side-list li::before{content:"›";position:absolute;left:0;top:-1px;font-weight:700}
.side-list li.current{font-weight:700;font-size:12.5px}

/* banner */
.banner{left:284px;top:185px;width:626px;height:181px;background:linear-gradient(100deg,#1f7fc8 0,#45b4e6 45%,#7fcfe9 70%,#3c8fc9 100%)}
.banner-copy{left:297px;top:281px;color:var(--white);font-family:"Open Sans",sans-serif}
.banner-copy h2{font-size:24px;font-weight:700;line-height:1.1;letter-spacing:-.3px}
.banner-copy p{font-size:16px;font-weight:600;line-height:1.22;margin-top:2px;letter-spacing:-.2px;white-space:nowrap}

/* aside */
.aside-photo{left:926px;top:185px;width:197px;height:152px;background:linear-gradient(135deg,#5b6f86,#c9d6e2 55%,#8a7058)}
.aside-band{left:926px;top:337px;width:197px;height:29px;background:var(--green);color:var(--white);font-family:"Roboto Condensed",sans-serif;font-size:14px;line-height:29px;padding-left:8px}
.aside-text{left:938px;top:380px;width:183px;font-size:13px;line-height:19px;text-align:justify;hyphens:manual}
.aside-text p+p{margin-top:19px}
.aside-rule{left:926px;top:366px;width:1px;height:350px;background:linear-gradient(#ddd,transparent)}

/* solutions */
.section-title{left:286px;top:374px;font-family:"Open Sans",sans-serif;font-weight:700;font-size:26px;color:var(--green)}
.card{top:412px;width:202px;height:312px;border:1px solid var(--line);border-radius:10px;background:var(--white);box-shadow:0 1px 3px rgba(0,0,0,.06)}
.card-photo{position:absolute;left:17px;top:11px;width:169px;height:124px}
.card-band{position:absolute;left:17px;top:91px;width:169px;height:45px;background:var(--green-band);color:var(--white);font-family:"Roboto Condensed",sans-serif;font-size:14px;line-height:15px;padding:9px 10px 0}
.card-text{position:absolute;left:17px;top:146px;width:172px;font-size:13px;line-height:16.5px}
.card-links{position:absolute;left:17px;list-style:none;font-size:13px;line-height:16.5px;color:var(--link)}
.card-links li{padding-left:12px;position:relative}
.card-links li::before{content:"›";position:absolute;left:1px;top:-1px;color:var(--green);font-weight:700}

/* footer */
.footer-links{left:58px;top:766px;font-size:13px;color:var(--white)}
.copyright{right:77px;top:766px;font-size:13px;color:var(--white)}
</style>
</head>
<body>

<div class="abs utility-bar"></div>
<div class="abs page"></div>

<nav class="abs utility-nav">
  <a class="signin" href="#"><svg viewBox="0 0 20 20"><circle cx="10" cy="10" r="9" fill="#fff"/><path d="M6 10h6M9.5 7l3 3-3 3" stroke="#3f8f35" stroke-width="1.8" fill="none"/></svg>SIGN IN / REGISTER</a>
  <a href="#"><svg viewBox="0 0 20 20"><circle cx="10" cy="10" r="9" fill="#fff"/><rect x="8" y="5" width="4" height="3" fill="#0d6cb8"/><rect x="5" y="11" width="4" height="3" fill="#0d6cb8"/><rect x="11" y="11" width="4" height="3" fill="#0d6cb8"/><path d="M10 8v2M7 10h6v1M7 10v1" stroke="#0d6cb8" fill="none"/></svg>CONTACT &nbsp;US</a>
  <a href="#"><svg viewBox="0 0 20 20"><circle cx="10" cy="10" r="9" fill="#fff"/><rect x="5.5" y="6.5" width="9" height="7" fill="none" stroke="#0d6cb8" stroke-width="1.3"/><path d="M5.5 6.5l4.5 4 4.5-4" stroke="#0d6cb8" stroke-width="1.3" fill="none"/></svg>SITEMAP</a>
</nav>

<div class="abs brand-name">BrightVale</div>

<nav class="abs main-nav">
  <a href="#">Home</a>
  <a class="active" href="#">Solutions</a>
  <a href="#">Why Us</a><span class="sep">|</span>
  <a href="#">Company</a><span class="sep">|</span>
  <a href="#">Careers</a>
</nav>

<aside class="abs side-nav">
  <div class="side-head"><span class="toggle"><svg width="9" height="7" viewBox="0 0 9 7"><path d="M0 0h9L4.5 7z" fill="#fff"/></svg></span>Sales Planning Analytics</div>
  <ul class="side-list">
    <li>Customer Targeting</li>
    <li>Territory Planning</li>
    <li class="current">Campaign Planning</li>
  </ul>
  <div class="side-head"><span class="toggle"><svg width="7" height="9" viewBox="0 0 7 9"><path d="M0 0v9l7-4.5z" fill="#fff"/></svg></span>Sales Productivity Centers</div>
  <div class="side-head"><span class="toggle"><svg width="7" height="9" viewBox="0 0 7 9"><path d="M0 0v9l7-4.5z" fill="#fff"/></svg></span>Sales Measurement Analytics</div>
</aside>

<div class="abs banner" role="img" aria-label="Two business people shaking hands in front of a rising stock chart"></div>
<div class="abs banner-copy">
  <h2>Do more with less.</h2>
  <p>No upfront software, hardware,<br>people or training costs for you. Pay as you go.</p>
</div>

<div class="abs aside-photo" role="img" aria-label="Hands reviewing paperwork at a meeting table"></div>
<div class="abs aside-band">Sales Operations Support</div>
<div class="abs aside-rule"></div>
<div class="abs aside-text">
  <p>Vestibulum lectus arcu, iaculis non iaculis ultrices, ultricies sit amet nisi. Nullam dictum nunc et metus dapibus scelerisque. Etiam quis sapien in purus consequat ornare.</p>
  <p>Praesent vitae ipsum lorem. Nullam ac orci mi, sed pellen&shy;tesque dolor. Nullam dictum nunc et metus dapibus scelerisque. Etiam quis sapien in purus consequat ornare. Praesent vitae ipsum lorem. Nullam ac orci mi, sed pellen&shy;tesque dolor.</p>
</div>

<h1 class="abs section-title">Solutions</h1>

<article class="abs card" style="left:282px">
  <div class="card-photo" role="img" aria-label="Hands pointing at printed reports" style="background:linear-gradient(135deg,#3d3d45,#b9bcc2 60%,#e5e5e5)"></div>
  <div class="card-band">Sales Planning<br>Analytics</div>
  <p class="card-text">We help target the right customers, allocate resources effectively and increase return on sales &amp; marketing $.</p>
  <ul class="card-links" style="top:235px">
    <li>Customer Targeting</li><li>Territory Planning</li><li>Campaign Planning</li>
  </ul>
</article>

<article class="abs card" style="left:495px">
  <div class="card-photo" role="img" aria-label="Sales team working on headsets at their desks" style="background:linear-gradient(135deg,#5a7fa8,#dfe7ef 55%,#b5c6d6)"></div>
  <div class="card-band">Sales Operations<br>Support</div>
  <p class="card-text">This is all about saving time for sales reps and improv&shy;ing their productivity.</p>
  <ul class="card-links" style="top:204px">
    <li>Quoting center</li><li>Proposal center</li><li>CRM center</li><li>Partner center</li><li>Reference center</li><li>Deal center</li>
  </ul>
</article>

<article class="abs card" style="left:708px">
  <div class="card-photo" role="img" aria-label="Red bar chart on a desk" style="background:linear-gradient(135deg,#c74a3a,#e9c9bf 55%,#f2f2f2)"></div>
  <div class="card-band">Sales Measurement<br>Analytics</div>
  <p class="card-text">This is all about improving sales efficiency by providing actionable insights.</p>
  <ul class="card-links" style="top:203px">
    <li>Business Reporting</li><li>Metrics &amp; Benchmarking</li><li>Pipeline health check</li><li>Sales rep scorecards</li><li>What-if analyses</li><li>Data services.</li>
  </ul>
</article>

<div class="abs footer-links">Contact Us | Sitemap &nbsp;| &nbsp;Disclaimer</div>
<div class="abs copyright">© 2010. BrightVale, Inc. All Rights Reserved</div>

</body>
</html>
```